Halvor Grading and Septic needs a flyer to submit to contractors to offer our services

I need a sleek profession one page full color high gloss document showcasing our services to give to Mobile Home Companies and contractors that need our services.

Target Market(s)

Home Builders. Mobile Home Salesmen. People Building new homes.

Industry/Entity Type

Construction

Font styles to use
Serif
Sans Serif

Requirements
Must have
• Phone Number. Email address. Logo. Services offered: Mobile Home Pads, Meter Pole Placement and Connection, Waterline Connection, On Site Septic System Installs
Should not have
• Jokes, Nothing trying to be cute

```html
<!DOCTYPE html>
<html lang="en">
<head>
<meta charset="utf-8">
<title>Halvor Grading and Septic – Services Flyer</title>
<link href="https://fonts.googleapis.com/css2?family=Oswald:wght@400;500;600;700&display=swap" rel="stylesheet">
<style>
  :root {
    --backdrop: #cfcfcf;
    --brand-blue: #174f85;
    --soil-teal: #1e3b47;
    --soil-teal-light: #28505c;
    --sky-light: #f3f4f5;
    --sky-mid: #e2e5e8;
    --white: #ffffff;
  }
  * { margin: 0; padding: 0; box-sizing: border-box; }
  html, body {
    width: 959px; height: 1200px; overflow: hidden;
    background: var(--backdrop);
    font-family: "Oswald", "Arial Narrow", sans-serif;
  }
  .flyer {
    position: absolute; left: 145px; top: 126px;
    width: 670px; height: 947px; overflow: hidden;
    background: var(--soil-teal);
  }
  .flyer-art { position: absolute; inset: 0; }
  .brand-name {
    position: absolute; top: 52px; left: 0; width: 100%;
    text-align: center; color: var(--brand-blue);
    font-weight: 700; font-size: 30px; line-height: 36px; letter-spacing: 1px;
  }
  .headline {
    position: absolute; top: 160px; left: 0; width: 100%;
    text-align: center; color: var(--brand-blue); text-transform: uppercase;
  }
  .headline-main {
    display: block; font-weight: 600; font-size: 66px; line-height: 72px; letter-spacing: -1.5px;
  }
  .headline-sub {
    display: block; font-weight: 600; font-size: 36px; line-height: 38px; letter-spacing: -0.6px;
  }
  .services {
    position: absolute; top: 545px; left: 185px; width: 300px;
    text-align: center; color: var(--white);
  }
  .services-title { font-weight: 600; font-size: 32px; line-height: 42px; letter-spacing: -0.3px; }
  .services-list { list-style: none; font-weight: 400; font-size: 19px; line-height: 26.5px; margin-top: 2px; }
  .contact-bar {
    position: absolute; left: 0; top: 858px; width: 670px; height: 89px;
    background: var(--brand-blue); color: var(--white);
  }
  .contact-item { position: absolute; top: 0; height: 89px; display: flex; align-items: center; }
  .contact-phone { left: 28px; }
  .contact-email { left: 351px; }
  .contact-icon { flex: none; }
  .phone-number { font-weight: 500; font-size: 40px; margin-left: 9px; letter-spacing: -0.5px; }
  .email-address { font-weight: 500; font-size: 16px; margin-left: 12px; }
</style>
</head>
<body>
  <main class="flyer">
    <svg class="flyer-art" width="670" height="947" viewBox="0 0 670 947" aria-hidden="false">
      <defs>
        <linearGradient id="skyFade" x1="0" y1="0" x2="0" y2="1">
          <stop offset="0" stop-color="var(--sky-mid)"/>
          <stop offset="1" stop-color="var(--sky-light)"/>
        </linearGradient>
        <linearGradient id="soilFade" x1="0" y1="0" x2="1" y2="1">
          <stop offset="0" stop-color="var(--soil-teal-light)"/>
          <stop offset="1" stop-color="var(--soil-teal)"/>
        </linearGradient>
        <linearGradient id="tankPhoto" x1="0" y1="0" x2="0" y2="1">
          <stop offset="0" stop-color="#3f78d4"/>
          <stop offset="0.55" stop-color="#c9c9c4"/>
          <stop offset="0.75" stop-color="#b0662f"/>
          <stop offset="1" stop-color="#6e8f3c"/>
        </linearGradient>
        <linearGradient id="digPhoto" x1="0" y1="0" x2="0" y2="1">
          <stop offset="0" stop-color="#6b8a54"/>
          <stop offset="0.35" stop-color="#d29c3a"/>
          <stop offset="0.7" stop-color="#cf9d6f"/>
          <stop offset="1" stop-color="#c8a281"/>
        </linearGradient>
      </defs>

      <rect class="soil-backdrop" width="670" height="947" fill="url(#soilFade)" role="img" aria-label="Dark-toned photo of an excavated trench in soil"/>
      <polygon class="sky-panel" points="0,0 670,0 670,127 335,630 0,127" fill="url(#skyFade)" role="img" aria-label="Faded photo of an excavator beside a mobile home"/>

      <g class="photo-frame photo-tank">
        <rect x="59" y="331" width="200" height="200" rx="42" fill="var(--white)" transform="rotate(45 159 431)"/>
        <rect x="67" y="339" width="184" height="184" rx="36" fill="url(#tankPhoto)" transform="rotate(45 159 431)" role="img" aria-label="Photo of a concrete septic tank being lowered by a crane"/>
      </g>
      <g class="photo-frame photo-dig">
        <rect x="412" y="331" width="200" height="200" rx="42" fill="var(--white)" transform="rotate(45 512 431)"/>
        <rect x="420" y="339" width="184" height="184" rx="36" fill="url(#digPhoto)" transform="rotate(45 512 431)" role="img" aria-label="Photo of an excavator beside an installed septic tank with green lids"/>
      </g>
      <g class="services-panel">
        <rect x="202" y="502" width="266" height="266" rx="50" fill="var(--white)" transform="rotate(45 335 635)"/>
        <rect x="213" y="513" width="244" height="244" rx="44" fill="var(--brand-blue)" transform="rotate(45 335 635)"/>
      </g>
    </svg>

    <div class="brand-name">HALVOR GRADING &amp; SEPTIC</div>

    <h1 class="headline">
      <span class="headline-main">Professional</span>
      <span class="headline-sub">Wastewater Management</span>
    </h1>

    <section class="services">
      <h2 class="services-title">OUR SERVICES</h2>
      <ul class="services-list">
        <li>Mobile Home Pads,</li>
        <li>Meter Pole Placement and Connection,</li>
        <li>Waterline Connection,</li>
        <li>On Site Septic</li>
        <li>System Installs</li>
      </ul>
    </section>

    <footer class="contact-bar">
      <div class="contact-item contact-phone">
        <svg class="contact-icon" width="40" height="40" viewBox="0 0 40 40" aria-hidden="true">
          <circle cx="20" cy="20" r="20" fill="var(--white)"/>
          <path d="M13.5 10.5c1-.8 2.2-.6 2.8.4l2 3.2c.5.9.3 1.9-.5 2.5l-1.4 1c.9 2.2 2.6 4 4.8 5l1-1.4c.6-.8 1.7-1 2.5-.5l3.2 2c1 .6 1.2 1.9.4 2.8l-1.3 1.5c-1 1.1-2.6 1.4-4 .8-5-2.1-8.9-6-11-11-.6-1.4-.3-3 .8-4z" fill="var(--brand-blue)"/>
        </svg>
        <span class="phone-number">(555) 014-2270</span>
      </div>
      <div class="contact-item contact-email">
        <svg class="contact-icon" width="30" height="30" viewBox="0 0 30 30" aria-hidden="true">
          <circle cx="15" cy="15" r="15" fill="var(--white)"/>
          <rect x="7.5" y="10" width="15" height="10" fill="none" stroke="var(--brand-blue)" stroke-width="1.6"/>
          <path d="M7.5 10l7.5 6 7.5-6M7.5 20l5.5-5M22.5 20l-5.5-5" fill="none" stroke="var(--brand-blue)" stroke-width="1.4"/>
        </svg>
        <span class="email-address">office@halvorgradingandseptic.com</span>
      </div>
    </footer>
  </main>
</body>
</html>
```